Modern stationary/business card design for KMR Interior Solutions
KMR Interior Solutions
Modern
Tobias Wrenfield
VP
8126 B Larchvale
Houston, TX 77081
tobias@stonecrestworks.com
www.stonecrestworks.com
We are open to tag lines so feel free to explore. I will give feedback to point you in the right direction.
Possibly a list of all the services we provide...
Granite, Quartz, Tile, Vinyl, Wood, Carpet, Mirrors, Cabinets, Hardware
I have more colors to choose from.

```html
<!DOCTYPE html>
<html lang="en">
<head>
<meta charset="utf-8">
<title>KMR Interior Solutions – Stationery</title>
<link rel="stylesheet" href="https://fonts.googleapis.com/css2?family=Open+Sans:wght@300;400;600;700&display=swap">
<style>
  :root {
    --brand-blue: #4d75a3;
    --band-blue: #5b7fa9;
    --band-dark: #46678e;
    --ink-grey: #6b7280;
    --paper: #ffffff;
    --backdrop: #eceef1;
    --watermark: #e6ebf2;
  }
  * { margin: 0; padding: 0; box-sizing: border-box; }
  html, body { width: 1200px; height: 936px; overflow: hidden; }
  body {
    background: var(--backdrop);
    font-family: "Open Sans", Arial, sans-serif;
    position: relative;
  }
  .sheet {
    position: absolute;
    background: var(--paper);
    box-shadow: 0 2px 6px rgba(0,0,0,0.12);
    overflow: hidden;
  }
  .wordmark { color: var(--brand-blue); font-weight: 400; line-height: 1; }
  .wordmark .mark-square {
    display: inline-block; background: var(--brand-blue); vertical-align: middle;
  }
  .web-band {
    position: absolute; left: 0; right: 0; bottom: 0;
    background: var(--band-blue);
    color: #fff; font-weight: 600; text-align: center;
    letter-spacing: 0.25em;
  }

  /* Letterhead */
  .letterhead { left: 185px; top: 69px; width: 386px; height: 543px; }
  .letterhead .wordmark { position: absolute; left: 28px; top: 26px; display: flex; align-items: center; gap: 8px; }
  .letterhead .mark-square { width: 22px; height: 22px; }
  .letterhead .name { font-size: 24px; }
  .letterhead .tagline { position: absolute; left: 58px; top: 54px; font-size: 11px; color: var(--brand-blue); }
  .letterhead .contact { position: absolute; left: 262px; top: 24px; font-size: 6.5px; line-height: 9px; color: var(--ink-grey); }
  .letterhead .watermark-name {
    position: absolute; left: 0; right: 0; top: 230px; text-align: center;
    font-size: 96px; color: var(--watermark); font-weight: 400;
  }
  .letterhead .web-band { height: 16px; bottom: 16px; font-size: 8px; line-height: 16px; }

  /* Presentation folder */
  .folder { left: 635px; top: 46px; width: 462px; height: 571px; }
  .folder .logo-block { position: absolute; left: 0; right: 0; top: 200px; text-align: center; }
  .folder .mark-square { width: 58px; height: 58px; margin-bottom: 14px; }
  .folder .name { font-size: 62px; display: block; }
  .folder .tagline { font-size: 24px; color: var(--brand-blue); font-weight: 400; margin-top: 6px; }
  .folder .rule { position: absolute; left: 0; right: 0; bottom: 40px; height: 2px; background: var(--band-blue); }
  .folder .web-band { height: 20px; bottom: 14px; font-size: 10px; line-height: 20px; }

  /* Business cards */
  .card-front { left: 38px; top: 655px; width: 203px; height: 97px; }
  .card-front .wordmark { position: absolute; left: 12px; top: 14px; display: flex; align-items: center; gap: 4px; }
  .card-front .mark-square { width: 10px; height: 10px; }
  .card-front .name { font-size: 13px; }
  .card-front .tagline { position: absolute; left: 12px; top: 30px; font-size: 6px; color: var(--brand-blue); }
  .card-front .details { position: absolute; left: 92px; top: 12px; font-size: 5px; line-height: 7px; color: var(--ink-grey); }
  .card-front .details .person { color: var(--brand-blue); font-weight: 600; }
  .card-front .web-band { height: 8px; bottom: 4px; }

  .card-back { left: 38px; top: 770px; width: 203px; height: 102px; }
  .card-back .surface {
    position: absolute; inset: 0;
    background: linear-gradient(110deg, var(--band-dark) 0%, var(--band-blue) 55%, #7f9cc0 100%);
  }
  .card-back .site { position: absolute; left: 10px; bottom: 8px; font-size: 5px; color: #fff; letter-spacing: 0.1em; }

  /* Envelope front */
  .envelope-front { left: 267px; top: 673px; width: 432px; height: 206px; }
  .envelope-front .wordmark { position: absolute; left: 18px; top: 22px; display: flex; align-items: center; gap: 6px; }
  .envelope-front .mark-square { width: 16px; height: 16px; }
  .envelope-front .name { font-size: 20px; }
  .envelope-front .tagline { position: absolute; left: 40px; top: 45px; font-size: 8px; color: var(--brand-blue); }
  .envelope-front .address { position: absolute; left: 18px; top: 70px; font-size: 6px; color: var(--ink-grey); }
  .envelope-front .web-band { height: 14px; bottom: 12px; font-size: 7px; line-height: 14px; }

  /* Envelope back */
  .envelope-back { left: 737px; top: 675px; width: 432px; height: 203px; }
  .envelope-back .flap { position: absolute; left: 0; top: 0; width: 432px; height: 110px; }
  .envelope-back .flap-site {
    position: absolute; left: 0; right: 0; top: 14px; text-align: center;
    font-size: 8px; font-weight: 600; color: #fff; letter-spacing: 0.25em;
  }
</style>
</head>
<body>

  <section class="sheet letterhead">
    <div class="wordmark"><span class="mark-square"></span><span class="name">KMR</span></div>
    <div class="tagline">Interior Solutions</div>
    <address class="contact">
      8126 B Larchvale<br>
      Houston, TX 77081<br>
      tobias@stonecrestworks.com<br>
      www.stonecrestworks.com
    </address>
    <div class="watermark-name">KMR</div>
    <div class="web-band">www.stonecrestworks.com</div>
  </section>

  <section class="sheet folder">
    <div class="logo-block">
      <span class="wordmark"><span class="mark-square"></span><span class="name">KMR</span></span>
      <div class="tagline">Interior Solutions</div>
    </div>
    <div class="rule"></div>
    <div class="web-band">www.stonecrestworks.com</div>
  </section>

  <section class="sheet card-front">
    <div class="wordmark"><span class="mark-square"></span><span class="name">KMR</span></div>
    <div class="tagline">Interior Solutions</div>
    <div class="details">
      <span class="person">Tobias Wrenfield</span><br>
      VP<br>
      8126 B Larchvale<br>
      Houston, TX 77081<br>
      tobias@stonecrestworks.com<br>
      www.stonecrestworks.com
    </div>
    <div class="web-band"></div>
  </section>

  <section class="sheet card-back">
    <div class="surface" role="img" aria-label="Blue faceted geometric pattern"></div>
    <div class="site">www.stonecrestworks.com</div>
  </section>

  <section class="sheet envelope-front">
    <div class="wordmark"><span class="mark-square"></span><span class="name">KMR</span></div>
    <div class="tagline">Interior Solutions</div>
    <div class="address">8126 B Larchvale Houston, TX 77081</div>
    <div class="web-band">www.stonecrestworks.com</div>
  </section>

  <section class="sheet envelope-back">
    <svg class="flap" viewBox="0 0 432 110" aria-hidden="true">
      <rect x="0" y="0" width="432" height="38" fill="#5b7fa9"/>
      <path d="M0 38 L0 46 Q216 120 432 46 L432 38 Z" fill="#5b7fa9"/>
      <path d="M0 46 Q216 120 432 46" fill="none" stroke="#d7dee8" stroke-width="1"/>
    </svg>
    <div class="flap-site">www.stonecrestworks.com</div>
  </section>

</body>
</html>
```